BildeVOLD buisnesscard

Hey :) I need a modern buisnesscard for my company BildeVOLD
It most have:
Dagligleder og Fotograf: Henrik Audun Strandvik

Mob: +4700000000
Epost: post@bildevold.example
Adresse: Kvernbakken9, 0000 Fjellvika

Facbook and instagram logo with text BildeVOLD

BildeVOLD logo

It Company

```html
<!DOCTYPE html>
<html lang="no">
<head>
<meta charset="utf-8">
<title>BildeVOLD – visittkort</title>
<link href="https://fonts.googleapis.com/css2?family=Jost:wght@400;500;700&display=swap" rel="stylesheet">
<style>
  :root {
    --brand-blue: #2277a8;
    --brand-pink: #c8407f;
    --card-white: #f4f4f4;
    --card-dark: #2a2a2a;
    --card-dark-shade: #323232;
    --stage: #d9d9d9;
    --text-light: #ffffff;
    --rule-light: rgba(255,255,255,.55);
    --social-blue: #3b5ba8;
  }
  * { margin: 0; padding: 0; box-sizing: border-box; }
  html, body {
    width: 1200px; height: 799px; overflow: hidden;
    background: var(--stage);
    font-family: "Jost", "Futura", sans-serif;
  }
  .stage {
    position: relative; width: 1200px; height: 799px;
    display: flex; justify-content: center; align-items: center; gap: 90px;
  }
  .card {
    position: relative; width: 350px; height: 570px; overflow: hidden;
    box-shadow: 0 10px 30px rgba(0,0,0,.25);
  }

  /* Front */
  .card-front { background: var(--card-white); }
  .card-front .band { position: absolute; inset: 0; width: 100%; height: 100%; }
  .brand-block { position: absolute; top: 70px; left: 0; right: 0; text-align: center; }
  .brand-name {
    font-weight: 700; font-size: 40px; letter-spacing: .5px; color: var(--brand-blue);
    white-space: nowrap;
  }
  .brand-mark {
    display: block; width: 54px; height: 54px; margin: 0 auto 14px;
    border-radius: 50%; background: var(--brand-pink);
  }
  .person { position: absolute; top: 215px; left: 0; right: 0; text-align: center; }
  .person-name { font-size: 22px; font-weight: 500; color: var(--brand-blue); white-space: nowrap; }
  .person-role { font-size: 15px; color: var(--brand-pink); margin-top: 2px; }
  .contact {
    position: absolute; left: 30px; bottom: 34px; color: var(--text-light);
    font-size: 16px; line-height: 1.35;
  }
  .contact .address { margin-bottom: 10px; }
  .contact-row { display: flex; align-items: center; gap: 10px; }
  .contact-row svg { width: 16px; height: 16px; flex: none; }

  /* Back */
  .card-back { background: var(--card-dark); }
  .card-back .shade { position: absolute; inset: 0; width: 100%; height: 100%; }
  .back-brand { position: absolute; top: 215px; left: 0; right: 0; text-align: center; }
  .back-brand .brand-name { font-size: 44px; }
  .social-row {
    display: flex; align-items: center; justify-content: center; gap: 10px; margin-top: 18px;
  }
  .social-row .rule { width: 80px; height: 1px; background: var(--rule-light); }
  .social-dot { width: 28px; height: 28px; border-radius: 50%; }
  .social-dot.blue { background: var(--social-blue); }
  .social-dot.pink { background: var(--brand-pink); }
</style>
</head>
<body>
<main class="stage">

  <section class="card card-front">
    <svg class="band" viewBox="0 0 350 570" preserveAspectRatio="none" aria-hidden="true">
      <polygon points="0,320 350,440 350,452 0,332" fill="var(--brand-pink)"/>
      <polygon points="0,338 350,458 350,570 0,570" fill="var(--brand-blue)"/>
    </svg>
    <div class="brand-block">
      <span class="brand-mark"></span>
      <div class="brand-name">BildeVOLD</div>
    </div>
    <div class="person">
      <div class="person-name">Henrik Audun Strandvik</div>
      <div class="person-role">Dagligleder og Fotograf</div>
    </div>
    <div class="contact">
      <div class="address">Kvernbakken9<br>0000 Fjellvika</div>
      <div class="contact-row">
        <svg viewBox="0 0 16 16"><rect x="4" y="1" width="8" height="14" rx="1.5" fill="none" stroke="#fff" stroke-width="1.4"/><circle cx="8" cy="12.5" r=".9" fill="#fff"/></svg>
        <span>+4700000000</span>
      </div>
      <div class="contact-row">
        <svg viewBox="0 0 16 16"><rect x="1" y="3.5" width="14" height="9" fill="#fff"/><polyline points="1,3.5 8,9 15,3.5" fill="none" stroke="var(--brand-blue)" stroke-width="1.2"/></svg>
        <span>post@bildevold.example</span>
      </div>
      <div class="contact-row">
        <svg viewBox="0 0 16 16"><circle cx="8" cy="8" r="6.5" fill="#fff"/><path d="M5 5c2 0 2 2 4 2s1 3-1 4" fill="none" stroke="var(--brand-blue)" stroke-width="1.4"/></svg>
        <span>www.bildevold.example</span>
      </div>
    </div>
  </section>

  <section class="card card-back">
    <svg class="shade" viewBox="0 0 350 570" preserveAspectRatio="none" aria-hidden="true">
      <polygon points="0,0 350,0 350,250 0,120" fill="var(--card-dark-shade)"/>
      <polygon points="0,430 350,330 350,570 0,570" fill="var(--card-dark-shade)"/>
    </svg>
    <div class="back-brand">
      <span class="brand-mark"></span>
      <div class="brand-name">BildeVOLD</div>
      <div class="social-row">
        <span class="rule"></span>
        <span class="social-dot blue"></span>
        <span class="social-dot pink"></span>
        <span class="rule"></span>
      </div>
    </div>
  </section>

</main>
</body>
</html>
```